Harbourline Electrical Solutions

On one side. LOGO (underneath:) Commercial Industrial Residential

- NAME & CONTACT DETAILS

Marcus T. Hollings
Project Manager

(Cell icon) (441) 555-0187
(Email icon) hlelectricalsolutions@mailvento.com
(Facebook & Instagram icons )@hlelectricalsolutions

Other side: LOGO - underneath ELECTRICAL CONSTRUCTION & MAINTENANCE . LED LIGHTING & AUTOMATION . LIFE SAFETY SYSTEMS (FIRE ALARM / SECURITY) . DATA & COMMUNICATION

```html
<!DOCTYPE html>
<html lang="en">
<head>
<meta charset="utf-8">
<title>Harbourline Electrical Solutions – Business Card</title>
<link rel="stylesheet" href="https://fonts.googleapis.com/css2?family=Montserrat:wght@400;500;700&display=swap">
<style>
  :root {
    --teal: #10566b;
    --ink: #2b2b2b;
    --grey: #555555;
    --paper: #ffffff;
    --backdrop: #262628;
  }
  * { box-sizing: border-box; margin: 0; padding: 0; }
  html, body { width: 1200px; height: 1200px; overflow: hidden; }
  body {
    background: var(--backdrop);
    font-family: "Montserrat", sans-serif;
    position: relative;
  }
  .card {
    position: absolute;
    left: 240px;
    width: 720px;
    height: 432px;
    background: var(--paper);
    overflow: hidden;
  }
  .card--front { top: 150px; }
  .card--back { top: 630px; }

  /* Front side */
  .services-panel {
    position: absolute;
    left: 0; top: 0;
    width: 537px; height: 100%;
    background: var(--teal);
  }
  .services {
    position: absolute;
    left: 96px; top: 164px;
    list-style: none;
    color: var(--paper);
    font-size: 14px;
    font-weight: 500;
    line-height: 17px;
  }
  .services li {
    position: relative;
    padding-left: 10px;
    margin-bottom: 10px;
  }
  .services li::before {
    content: "";
    position: absolute;
    left: 0; top: 5px;
    width: 5px; height: 5px;
    background: var(--paper);
  }
  .brand-strip {
    position: absolute;
    left: 537px; top: 0;
    width: 183px; height: 100%;
  }
  .brand-strip__name {
    position: absolute;
    left: 91px; top: 216px;
    transform: translate(-50%, -50%) rotate(-90deg);
    white-space: nowrap;
    color: var(--teal);
    font-size: 19px;
    font-weight: 500;
    letter-spacing: 2px;
    line-height: 23px;
    text-align: center;
  }

  /* Back side */
  .brand-lockup {
    position: absolute;
    right: 58px; top: 40px;
    display: flex;
    align-items: center;
    gap: 12px;
  }
  .brand-lockup__mark {
    width: 14px; height: 14px;
    background: var(--teal);
  }
  .brand-lockup__name {
    color: var(--teal);
    font-size: 17px;
    font-weight: 500;
    letter-spacing: 2.4px;
    line-height: 19px;
  }
  .sectors {
    position: absolute;
    right: 58px; top: 133px;
    color: var(--ink);
    font-size: 11px;
    font-weight: 500;
    letter-spacing: 2.4px;
  }
  .sectors .sep { color: var(--teal); margin: 0 6px; }

  .contact-name {
    position: absolute;
    left: 54px; top: 288px;
    color: var(--teal);
    font-size: 19px;
    font-weight: 700;
    letter-spacing: 0.2px;
  }
  .contact-role {
    position: absolute;
    left: 54px; top: 312px;
    color: var(--ink);
    font-size: 13px;
  }
  .contact-rule {
    position: absolute;
    left: 54px; top: 338px;
    width: 58px; height: 2px;
    background: var(--teal);
  }
  .contact-line {
    position: absolute;
    display: flex;
    align-items: center;
    gap: 5px;
    color: var(--ink);
    font-size: 13.5px;
  }
  .contact-line svg { width: 14px; height: 14px; flex: none; }
  .contact-line--phone { left: 54px; top: 353px; }
  .contact-line--email { left: 54px; top: 376px; }
  .contact-line--social { right: 60px; top: 376px; }
  .social-dot {
    width: 14px; height: 14px;
    border: 1.3px solid var(--teal);
    border-radius: 50%;
  }
</style>
</head>
<body>
  <section class="card card--front">
    <div class="services-panel">
      <ul class="services">
        <li>ELECTRICAL CONSTRUCTION<br>&amp; MAINTENANCE</li>
        <li>LED LIGHTING &amp; AUTOMATION</li>
        <li>LIFE SAFETY SYSTEMS<br>(FIRE ALARM / SECURITY)</li>
        <li>DATA &amp; COMMUNICATION</li>
      </ul>
    </div>
    <div class="brand-strip">
      <div class="brand-strip__name">HARBOURLINE<br>ELECTRICAL<br>SOLUTIONS</div>
    </div>
  </section>

  <section class="card card--back">
    <div class="brand-lockup">
      <span class="brand-lockup__mark"></span>
      <div class="brand-lockup__name">HARBOURLINE<br>ELECTRICAL<br>SOLUTIONS</div>
    </div>
    <div class="sectors">COMMERCIAL<span class="sep">|</span>INDUSTRIAL<span class="sep">|</span>RESIDENTIAL</div>

    <div class="contact-name">MARCUS T. HOLLINGS</div>
    <div class="contact-role">Project Manager</div>
    <div class="contact-rule"></div>

    <div class="contact-line contact-line--phone">
      <svg viewBox="0 0 16 16" aria-hidden="true">
        <circle cx="8" cy="8" r="7.2" fill="none" stroke="#10566b" stroke-width="1.2"/>
        <path d="M5.4 4.3l1.3 0 .6 1.7-.8.7c.4.9 1 1.5 1.9 1.9l.7-.8 1.7.6 0 1.3c0 .4-.3.7-.7.7C7.4 10.4 4.7 7.7 4.7 5c0-.4.3-.7.7-.7z" fill="#10566b"/>
      </svg>
      (441) 555-0187
    </div>
    <div class="contact-line contact-line--email">
      <svg viewBox="0 0 16 16" aria-hidden="true">
        <circle cx="8" cy="8" r="7.2" fill="none" stroke="#10566b" stroke-width="1.2"/>
        <rect x="4.3" y="5.3" width="7.4" height="5.4" fill="none" stroke="#10566b" stroke-width="1.1"/>
        <path d="M4.3 5.5L8 8.4l3.7-2.9" fill="none" stroke="#10566b" stroke-width="1.1"/>
      </svg>
      hlelectricalsolutions@mailvento.com
    </div>
    <div class="contact-line contact-line--social">
      <span class="social-dot"></span>
      <span class="social-dot"></span>
      @hlelectricalsolutions
    </div>
  </section>
</body>
</html>
```